Business card for Crestline Bathrooms

Please design a business card for our bathroom renovation business. You can use my existing logo, but if you have an idea to modernize it, I would like to see it. Please see attached files first. I would like to use the blue and the orange theme. I like the concept of using the shower head in the logo. Please find following a design (or two) that I have been trying to create with my limited resources. That design was for a sign, but I was going to adopt it and use it as a business card as well. I like the concept of the water splash but I don’t think it “flows” nicely together with the logo. Another thought is that maybe creating the logo out of water splash could work and have a dramatic effect (like the water text and the butterfly picture attached with similar background instead of white). If the above doesn’t work I would like to see a modern simplified design. One of the attached files named as the unwanted business card has all the details that I want included in the business card. Please note that it is two sided.
Updates

I am very thankful for the designs that I have received, but they are very similar and only a couple of attempts to do something with the water splash as per my original brief. Modernizing the logo and having it made out of out of water splash with the orange as color accent could work and have a dramatic effect (like the water text and the butterfly picture attached with similar background instead of white). Please do not use the butterfly itself! This is just an example that images can be created out of water splash.

Contact Information for Business Card

all the details are on the unwonted business card file included

Colors
3176b5

Requirements
Nice to have
• Copied from the brief:
• ... maybe creating the logo out of water splash could work and have a dramatic effect (like the water text and the butterfly picture attached with similar background instead of white). Please do not use the butterfly itself!
Should not have
• I am getting designs with a butterfly. The butterfly picture was an example of creating something from a water splash. The butterfly itself has no association with anything other than the concept of creating a logo out of water splash. Sorry, I thought I was clear in the brief.

```html
<!DOCTYPE html>
<html lang="en">
<head>
<meta charset="UTF-8">
<title>Crestline Bathrooms — Business Card</title>
<link href="https://fonts.googleapis.com/css2?family=Roboto:wght@400;500&family=Itim&display=swap" rel="stylesheet">
<style>
  :root {
    --navy: #02416b;
    --brand-blue: #0f4773;
    --accent: #ec7a6a;
    --sky: #bfe2fb;
    --sky-deep: #8ccaf2;
    --ink: #545b61;
    --backdrop: #e4e4e4;
    --white: #ffffff;
  }
  * { margin: 0; padding: 0; box-sizing: border-box; }
  html, body { width: 1200px; height: 960px; overflow: hidden; }
  body { background: var(--backdrop); font-family: "Roboto", Arial, sans-serif; }
  .stage { position: relative; width: 1200px; height: 960px; }

  .card {
    position: absolute;
    width: 600px;
    height: 342px;
    box-shadow: 2px 3px 6px rgba(0,0,0,0.28);
    overflow: hidden;
  }

  /* Front side */
  .card--front {
    left: 315px; top: 113px;
    background: linear-gradient(120deg, var(--white) 18%, #e6f4fe 50%, var(--sky) 100%);
  }
  .splash {
    position: absolute;
    left: 260px; top: -20px;
    width: 400px; height: 300px;
    background: radial-gradient(closest-side, rgba(140,202,242,0.9) 0%, rgba(140,202,242,0.45) 50%, rgba(191,226,251,0) 100%);
  }
  .wordmark {
    position: absolute;
    font-family: "Roboto", Arial, sans-serif;
    font-weight: 500;
    line-height: 1.05;
  }
  .card--front .wordmark {
    left: 44px; top: 58px;
    color: var(--brand-blue);
    font-size: 34px;
  }
  .wordmark .wordmark__sub { display: block; font-size: 22px; letter-spacing: 3px; margin-top: 4px; }

  .holder-name {
    position: absolute;
    left: 43px; top: 224px;
    font-family: "Itim", "Comic Sans MS", cursive;
    font-size: 25px;
    color: var(--brand-blue);
    letter-spacing: 0.5px;
  }
  .postal {
    position: absolute;
    left: 44px; top: 269px;
    font-size: 15px;
    line-height: 19px;
    color: var(--ink);
  }
  .contact-list {
    position: absolute;
    left: 344px; top: 231px;
    list-style: none;
    font-size: 15px;
    color: var(--ink);
  }
  .contact-list li { display: flex; align-items: center; height: 19px; white-space: nowrap; }
  .contact-list svg { width: 13px; height: 13px; margin-right: 9px; fill: var(--brand-blue); flex: none; }

  /* Back side */
  .card--back {
    left: 311px; top: 472px;
    background: var(--navy);
  }
  .card--back .wordmark {
    left: 54px; top: 112px;
    color: var(--white);
    font-size: 40px;
  }
  .card--back .wordmark .wordmark__sub { font-size: 25px; }
  .divider {
    position: absolute;
    left: 304px; top: 48px;
    width: 2px; height: 253px;
    background: var(--white);
  }
  .services {
    position: absolute;
    left: 338px; top: 45px;
    list-style: none;
    color: var(--white);
    font-size: 15px;
    line-height: 19px;
  }
  .services li { position: relative; padding-left: 17px; margin-bottom: 19px; }
  .services li::before {
    content: "";
    position: absolute;
    left: 0; top: 6px;
    width: 6px; height: 6px;
    border-radius: 50%;
    background: var(--accent);
  }
  .memberships {
    position: absolute;
    left: 339px; top: 265px;
    display: flex;
    align-items: center;
    height: 36px;
  }
  .badge { background: var(--white); }
  .badge--round { width: 32px; height: 34px; border-radius: 6px; }
  .badge--wide { width: 116px; height: 22px; border-radius: 2px; }
  .memberships__rule { width: 1px; height: 34px; background: var(--white); margin: 0 18px 0 17px; }
</style>
</head>
<body>
<main class="stage">

  <section class="card card--front" aria-label="Business card front">
    <div class="splash" role="img" aria-label="Blue water splash flowing across the card"></div>
    <div class="wordmark">Crestline<span class="wordmark__sub">Bathrooms</span></div>
    <p class="holder-name">Daniel Marsh</p>
    <p class="postal">PO Box 48<br>Hillcrest 2611</p>
    <ul class="contact-list">
      <li><svg viewBox="0 0 24 24" aria-hidden="true"><path d="M6.6 10.8a15.1 15.1 0 0 0 6.6 6.6l2.2-2.2c.3-.3.7-.4 1-.2 1.1.4 2.3.6 3.6.6.6 0 1 .4 1 1V20c0 .6-.4 1-1 1A17 17 0 0 1 3 4c0-.6.4-1 1-1h3.5c.6 0 1 .4 1 1 0 1.3.2 2.5.6 3.6.1.3 0 .7-.2 1z"/></svg>0400 555 210</li>
      <li><svg viewBox="0 0 24 24" aria-hidden="true"><path d="M7 1h10a2 2 0 0 1 2 2v18a2 2 0 0 1-2 2H7a2 2 0 0 1-2-2V3a2 2 0 0 1 2-2zm0 3v14h10V4zm5 15.5a1.2 1.2 0 1 0 0 2.4 1.2 1.2 0 0 0 0-2.4z"/></svg>6200 5147</li>
      <li><svg viewBox="0 0 24 24" aria-hidden="true"><path d="M2 5h20v14H2zm2 2v.4l8 5.2 8-5.2V7zm0 2.8V17h16V9.8l-8 5.2z"/></svg>dan@crestlinebathrooms.com.au</li>
      <li><svg viewBox="0 0 24 24" aria-hidden="true"><path d="M12 2a10 10 0 1 0 0 20 10 10 0 0 0 0-20zm-1 17.9A8 8 0 0 1 4.2 10L9 14.8v1a2 2 0 0 0 2 2zm6.9-2.5A2 2 0 0 0 16 16h-1v-3a1 1 0 0 0-1-1H8v-2h2a1 1 0 0 0 1-1V7h2a2 2 0 0 0 2-2v-.4a8 8 0 0 1 2.9 12.8z"/></svg>crestlinebathrooms.com.au</li>
    </ul>
  </section>

  <section class="card card--back" aria-label="Business card back">
    <div class="wordmark">Crestline<span class="wordmark__sub">Bathrooms</span></div>
    <div class="divider"></div>
    <ul class="services">
      <li>Complete Bathroom<br>Renovations &amp; Remodelling</li>
      <li>Highly Skilled &amp;<br>Qualified Tradespeople</li>
      <li>Professional Service From<br>Concept To Completion</li>
      <li>All Work Guaranteed</li>
    </ul>
    <div class="memberships" aria-label="Industry memberships">
      <div class="badge badge--round"></div>
      <div class="memberships__rule"></div>
      <div class="badge badge--wide"></div>
    </div>
  </section>

</main>
</body>
</html>
```